wardrobe/costume stylist needs good business card for own business

Hi:)

I'm wanting a business card for my company. I am a freelance stylist.

I do wardrobe/costume stylist to TV commercials; Films; Fashion and Lifestyle shoots.

I'd like a design based around my name Rosalind Parfrey written nicely, maybe a colour? Up to you?!

I've attached a couple of images of business cards I like
.... be creative and have fun!

Thank you :)

Reason: I was trying to get my new business card ready for before I headed overseas Friday morning but I don't think that was realistic so I'd like to extend the deadline to give time to the project. Thank you

Hi designers:) Thank you for all your designs, I've extended the deadline until Sunday, so there's a bit more time. I've attached 3 pictures of business cards which I quite like, please take a look to see if it can be of help in your process. I like the pale plain or patterned background with dark font and the dark plain or patterned background with the pale font the motifs the feminine fonts the plain fonts I like the idea of playing with a circle or some shape on one side of the card with my name or initials as in the picture I have on my post could you play around with this idea a bit please? Thank you all for the work you've done :) Rosa

Hi I am working overseas til Saturday night sorry for no feedback until I teturn Thanks :) Rosa

Hi designers, Thank you all so much for submitting your designs, I really appreciate your input into my project :) I'm sorry I didn't get to respond to some comments, and give feedback. I didn't back from being away until later than I expected, and the deadline had passed then, so apologies. Thanks to you all again for all your really good designs :) Rosa

Target Market(s)

I am a freelance stylist my target audience is producers, production companies, photographers, directors...

Industry/Entity Type

Business

Requirements
Must have
• Rosalind Parfrey
Stylist or Wardrobe Stylist

email rosaparfrey@mailbox-example.co.nz
Mobile 0218467193

(Don't have to use the words 'email' and 'mobile')
Nice to have
• Would like it to be double sided
Like B & W
Like pale colour background with dark font or white font
Like dark colour background with pale font
Should not have
• I would prefer it not to incorporate pictures

```html
<!DOCTYPE html>
<html lang="en">
<head>
<meta charset="utf-8">
<title>Rosalind Parfrey — Wardrobe Stylist business card</title>
<link rel="stylesheet" href="https://fonts.googleapis.com/css2?family=UnifrakturMaguntia&family=Josefin+Sans:wght@300;400&family=Pathway+Gothic+One&display=swap">
<style>
  :root {
    --backdrop: #e9e7e4;
    --cocoa: #5a2a17;
    --paper: #f7f6f3;
    --cream: #ffffff;
    --teal: #3fa6b4;
    --rule: #b9b5ae;
  }
  * { margin: 0; padding: 0; box-sizing: border-box; }
  html, body {
    width: 1200px;
    height: 900px;
    overflow: hidden;
    background: var(--backdrop);
  }
  .canvas {
    width: 1200px;
    height: 900px;
    display: flex;
    align-items: center;
    justify-content: center;
    gap: 120px;
  }
  .card {
    position: relative;
    width: 300px;
    height: 520px;
    border-radius: 4px;
    overflow: hidden;
    box-shadow: 0 6px 18px rgba(0, 0, 0, 0.18);
  }
  .card--back { background: var(--cocoa); color: var(--cream); }
  .card--front { background: var(--paper); color: var(--cocoa); }

  .ornament {
    position: absolute;
    left: 0;
    top: 0;
    width: 100%;
    height: 180px;
  }
  .card--back .ornament {
    background: linear-gradient(180deg, rgba(255,255,255,0.85) 0%, rgba(255,255,255,0.35) 55%, rgba(255,255,255,0) 100%);
  }
  .card--front .ornament {
    background: linear-gradient(180deg, var(--cocoa) 0%, rgba(90,42,23,0.45) 55%, rgba(90,42,23,0) 100%);
  }

  .identity {
    position: absolute;
    writing-mode: vertical-rl;
  }
  .name {
    font-family: "UnifrakturMaguntia", serif;
    font-weight: 400;
    line-height: 1.1;
    white-space: nowrap;
  }
  .role {
    font-family: "Josefin Sans", sans-serif;
    font-weight: 300;
    text-transform: uppercase;
    white-space: nowrap;
  }

  /* Back: dark card with contact details */
  .card--back .identity {
    top: 200px;
    right: 70px;
  }
  .card--back .name { font-size: 32px; }
  .card--back .role {
    font-size: 11px;
    letter-spacing: 1px;
    margin-block-start: 2px;
  }
  .contact {
    margin-block-start: 24px;
  }
  .contact__line {
    white-space: nowrap;
    margin-block-end: 10px;
  }
  .contact__label {
    display: inline-block;
    inline-size: 24px;
    font-family: "Josefin Sans", sans-serif;
    font-weight: 400;
    font-size: 19px;
  }
  .contact__value {
    font-family: "Pathway Gothic One", sans-serif;
    font-size: 20px;
    letter-spacing: 0.3px;
  }

  /* Front: pale card with name lockup */
  .card--front .identity {
    top: 190px;
    right: 100px;
  }
  .card--front .name { font-size: 40px; }
  .card--front .role {
    display: inline-block;
    color: var(--teal);
    font-size: 15px;
    letter-spacing: 5px;
    margin-block-start: 6px;
    padding: 4px 4px;
    border-block-start: 1px solid var(--rule);
    border-block-end: 1px solid var(--rule);
  }
</style>
</head>
<body>
  <main class="canvas">
    <section class="card card--back" aria-label="Card back">
      <div class="ornament" role="img" aria-label="White flowing swirl ornament with curls and droplets"></div>
      <div class="identity">
        <h2 class="name">Rosalind Parfrey</h2>
        <p class="role">Wardrobe Stylist</p>
        <div class="contact">
          <p class="contact__line"><span class="contact__label">M</span><span class="contact__value">0218467193</span></p>
          <p class="contact__line"><span class="contact__label">E</span><span class="contact__value">rosaparfrey@mailbox-example.co.nz</span></p>
        </div>
      </div>
    </section>

    <section class="card card--front" aria-label="Card front">
      <div class="ornament" role="img" aria-label="Brown flowing swirl ornament with curls and droplets"></div>
      <div class="identity">
        <h1 class="name">Rosalind Parfrey</h1>
        <p class="role">Wardrobe Stylist</p>
      </div>
    </section>
  </main>
</body>
</html>
```